Vindgerdi - Start-up company selling electricity

Hello let me tell you about Vindgerdi.

Vindgerdi is start-up company selling electricity in Iceland. The operations of the company consist of making power usage forecasts for our customers, purchasing the electricity wholesale from the energy producers, and selling the electricity to the consumer. We are focused on tech by using optimization and machine learning to minimize electricity prices to our customers. Our marketing strategy is to portray a tech company mindset and to show dedication to driving down the electricity price on the market.

We need your help to make our website pop. Possible concepts to work with are as follows:

- Iceland the land of ice and fire
- Green energy
- Innovation
- Tech and data science

Link to our website: https://prufa.vindgerdi-example.is/
We are open to ideas.
Thank you!

Target Market(s)

Electricity consumers both homes and companies.

Number of Pages Required

1 page

Font styles to use
Serif
Sans Serif

```html
<!DOCTYPE html>
<html lang="en">
<head>
<meta charset="utf-8">
<title>Vindgerdi – Same electricity, just cheaper</title>
<link rel="stylesheet" href="https://fonts.googleapis.com/css2?family=Barlow+Semi+Condensed:wght@500;600&family=Libre+Baskerville:wght@700&family=Poppins:wght@300;400;600&display=swap">
<style>
:root{
  --navy:#0b3566;
  --red:#993333;
  --maroon:#6b3232;
  --ink:#555b66;
  --white:#fff;
  --sans:"Poppins",sans-serif;
  --cond:"Barlow Semi Condensed",sans-serif;
  --serif:"Libre Baskerville",serif;
}
*{margin:0;padding:0;box-sizing:border-box}
html,body{width:1200px;height:2441px;overflow:hidden;background:var(--white)}
body{position:relative;font-family:var(--sans);color:var(--ink)}
.abs{position:absolute}
.backdrop{position:absolute;left:0;top:0;width:1200px;height:2441px}
.topbar{left:0;top:0;width:1200px;height:38px;background:var(--navy);color:var(--white);font-size:12px}
.topbar span{position:absolute;top:11px}
.topbar .divider{position:absolute;left:953px;top:10px;width:1px;height:18px;background:rgba(255,255,255,.35)}
.brand{display:flex;align-items:center;gap:8px;font-family:var(--serif);font-weight:700;font-size:26px;color:var(--navy)}
.brand .dot{width:30px;height:30px;border-radius:50%;background:var(--red)}
.nav a{position:absolute;top:56px;font-size:13px;color:#4a4f58;text-decoration:none}
.nav a.active{color:var(--red)}
.hero-title{left:0;width:1200px;top:258px;text-align:center;font-family:var(--serif);font-weight:700;font-size:46px;color:var(--white);letter-spacing:1px}
.hero-sub{left:300px;width:600px;top:325px;text-align:center;font-family:var(--cond);font-weight:600;font-size:15px;line-height:22px;color:var(--white)}
.btn{display:flex;align-items:center;justify-content:center;border-radius:5px;font-family:var(--cond);font-weight:600;font-size:14px;text-transform:uppercase}
.btn-light{left:529px;top:387px;width:135px;height:38px;background:var(--white);color:var(--navy)}
.btn-red{background:var(--red);color:var(--white)}
.btn-navy{background:var(--navy);color:var(--white)}
.heading{font-family:var(--cond);font-weight:600;font-size:31px;color:var(--navy)}
.heading em{font-style:normal;color:var(--red)}
.rule{display:flex;gap:4px;height:2px}
.rule i{display:block;height:2px;background:var(--red)}
.rule i:nth-child(2){opacity:.6}.rule i:nth-child(3){opacity:.3}
.about-text{left:497px;top:905px;width:480px;font-size:12.5px;line-height:19.5px}
.about-text p{margin-bottom:5px}
.photo{background:linear-gradient(135deg,#e8e2d6,#c9a46a 55%,#6a4a2a)}
.card{background:var(--white);box-shadow:0 0 12px rgba(0,0,0,.08);text-align:center}
.card-title{font-size:18.5px;color:var(--navy)}
.price{font-family:var(--sans);font-weight:600;font-size:22px;color:var(--red)}
.unit{font-size:12px;color:var(--ink)}
.card p{font-size:12.5px;line-height:19.5px}
.foot-h{font-size:19px;color:var(--white)}
.foot-list{list-style:none;font-size:12.5px;color:var(--white)}
.icon{width:34px;height:34px;background:var(--white);display:flex;align-items:center;justify-content:center}
.contact-line{font-size:12px;color:var(--white)}
.copyright{left:0;top:2405px;width:1200px;height:36px;background:var(--red);color:var(--white);font-size:12px;text-align:center;line-height:36px}
</style>
</head>
<body>

<svg class="backdrop" viewBox="0 0 1266 2576" aria-hidden="true">
  <defs>
    <linearGradient id="sky" x1="0" y1="0" x2="0" y2="1">
      <stop offset="0" stop-color="#4a5866"/>
      <stop offset=".35" stop-color="#9a9d9c"/>
      <stop offset=".55" stop-color="#b89f72"/>
      <stop offset=".8" stop-color="#3c3b33"/>
      <stop offset="1" stop-color="#5c6a4a"/>
    </linearGradient>
  </defs>
  <rect x="0" y="95" width="1266" height="805" fill="url(#sky)" role="img" aria-label="Photo of a geothermal power plant with steam rising against a sunset sky"/>
  <polygon points="580,575 1266,800 1266,888 610,683 560,750 440,690" fill="#993333"/>
  <polygon points="0,530 580,712 536,778 0,608" fill="#6b3232"/>
  <polygon points="0,608 536,778 610,683 1266,888 1266,905 0,905" fill="#fff"/>

  <rect x="63" y="855" width="380" height="435" fill="#0b3566"/>
  <rect x="189" y="850" width="254" height="198" fill="#fff"/>
  <polyline points="232,855 441,855 441,1015" fill="none" stroke="#0b3566" stroke-width="1.2"/>

  <polygon points="0,1980 690,2215 800,2110 1266,2260 1266,2576 0,2576" fill="#0b3566"/>
  <polygon points="730,2010 1266,2180 1266,2258 800,2110 700,2050" fill="#6b3232"/>
  <polygon points="0,1898 655,2104 700,2050 800,2110 690,2215 0,1980" fill="#993333"/>
</svg>

<div class="abs topbar">
  <span style="left:791px">VAT number: 100000</span>
  <i class="divider"></i>
  <span style="left:990px">ID Number: 000000-0000</span>
</div>

<div class="abs brand" style="left:60px;top:44px"><span class="dot"></span>Vindgerdi</div>

<nav class="nav">
  <a class="active" href="#" style="left:666px">Home</a>
  <a href="#" style="left:737px">Terms of Business</a>
  <a href="#" style="left:884px">Question &amp; Answer</a>
  <a href="#" style="left:1035px">About Vindgerdi</a>
</nav>

<h1 class="abs hero-title">VINDGERDI</h1>
<p class="abs hero-sub">We are focused on tech by using optimization and machine learning to minimize electricity prices to our customers</p>
<a class="abs btn btn-light">Learn more</a>

<div class="abs photo" style="left:90px;top:840px;width:300px;height:353px" role="img" aria-label="Light bulb glowing among handwritten formulas and sketches"></div>

<h2 class="abs heading" style="left:497px;top:850px">About <em>Us</em></h2>
<div class="abs rule" style="left:495px;top:887px"><i style="width:29px"></i><i style="width:8px"></i><i style="width:4px"></i></div>
<div class="abs about-text">
  <p>The customer can terminate the contract with Vindgerdi with three weeks' notice and the termination will then take effect at the end of next month. A longer notice period may be negotiated if the general user uses more than 0.5 GWh annually.</p>
  <p>Customers may terminate a contract with Vindgerdi if Vindgerdi significantly breaches its obligations.</p>
  <p>Vindgerdi may terminate the contract if the customer is not in arrears with payments. In the event of default by the customer, Vindgerdi will send a written demand for payment together with a warning that no payment will be made, which will result in termination of the contract.</p>
</div>
<a class="abs btn btn-red" style="left:495px;top:1126px;width:135px;height:37px">Learn more</a>

<h2 class="abs heading" style="left:0;width:1095px;text-align:center;top:1292px">Same electricity <em>~ just cheaper!</em></h2>
<div class="abs rule" style="left:523px;top:1337px"><i style="width:29px"></i><i style="width:8px"></i><i style="width:4px"></i></div>

<div class="abs card" style="left:112px;top:1422px;width:300px;height:337px"></div>
<div class="abs photo" style="left:128px;top:1395px;width:270px;height:158px;background:linear-gradient(135deg,#d8d0c4,#7a5a3c 60%,#3a2a20)" role="img" aria-label="Two business people shaking hands over a desk with a contract and laptop"></div>
<div class="abs card-title" style="left:112px;width:300px;top:1572px;text-align:center">Welcome to business</div>
<a class="abs btn btn-red" style="left:191px;top:1610px;width:135px;height:37px">Campany</a>
<a class="abs btn btn-navy" style="left:191px;top:1662px;width:135px;height:37px">Home</a>

<div class="abs card" style="left:449px;top:1422px;width:300px;height:337px"></div>
<div class="abs photo" style="left:465px;top:1395px;width:270px;height:158px;background:linear-gradient(135deg,#cfe0f2,#f4f6f9 50%,#3a7cc4)" role="img" aria-label="Hand holding a pen over printed charts next to a calculator"></div>
<div class="abs" style="left:449px;width:300px;top:1572px;text-align:center">
  <div class="card-title">Price list</div>
  <div class="price" style="margin-top:4px">6.95</div>
  <div class="unit">ISK / kWh</div>
  <div class="price" style="margin-top:10px">6.22</div>
  <div class="unit">ISK / kWh</div>
  <div class="unit" style="font-size:12.5px">electric acceleration</div>
</div>

<div class="abs card" style="left:787px;top:1422px;width:300px;height:337px"></div>
<div class="abs photo" style="left:802px;top:1395px;width:270px;height:158px;background:radial-gradient(circle at 70% 45%,#4aa8ff,#0d3a9a 55%,#061a4a)" role="img" aria-label="Glowing digital light bulb on a deep blue background"></div>
<div class="abs" style="left:802px;width:270px;top:1568px;text-align:center">
  <div class="card-title">The future is exciting</div>
  <p style="margin-top:6px">exciting Let's make the electricity system smarter together. Vindgerdi uses artificial intelligence, data science and automation to minimize costs and promote eccentricity</p>
</div>

<div class="abs brand" style="left:62px;top:2145px;color:var(--white);font-size:24px"><span class="dot"></span>Vindgerdi</div>
<p class="abs" style="left:62px;top:2192px;width:240px;font-size:12.5px;line-height:20px;color:var(--white)">Our marketing strategy is to portray a tech company mindset and to show dedication to driving down the electricity price on the market.</p>

<div class="abs foot-h" style="left:337px;top:2135px">Site Map</div>
<ul class="abs foot-list" style="left:337px;top:2170px;line-height:30px">
  <li>- Home</li><li>- Terms of Business</li><li>- Question &amp; Answer</li><li>- About Vindgerdi</li>
</ul>

<div class="abs foot-h" style="left:612px;top:2135px">Contact Us</div>
<div class="abs icon" style="left:611px;top:2171px"><svg width="18" height="20" viewBox="0 0 18 20"><path d="M9 1a6 6 0 0 0-6 6c0 5 6 11 6 11s6-6 6-11a6 6 0 0 0-6-6z" fill="none" stroke="#993333" stroke-width="1.8"/><circle cx="9" cy="7" r="2.2" fill="#993333"/></svg></div>
<div class="abs contact-line" style="left:658px;top:2180px">Lindargata 7 101 Reykjavik</div>
<div class="abs icon" style="left:611px;top:2223px"><svg width="20" height="14" viewBox="0 0 20 14"><rect width="20" height="14" rx="1" fill="#993333"/><path d="M1 1l9 7 9-7" fill="none" stroke="#fff" stroke-width="1.6"/></svg></div>
<div class="abs contact-line" style="left:658px;top:2233px">info@vindgerdi-example.is</div>
<div class="abs icon" style="left:611px;top:2277px"><svg width="18" height="18" viewBox="0 0 18 18"><path d="M4 1l3 4-2 2c1 2.5 3.5 5 6 6l2-2 4 3-2 3C8 16 2 10 1 4z" fill="#993333"/></svg></div>
<div class="abs contact-line" style="left:658px;top:2288px">555-0199</div>

<div class="abs foot-h" style="left:888px;top:2135px">Terms of Business</div>
<ul class="abs foot-list" style="left:888px;top:2176px;line-height:22.5px">
  <li>- Scope</li><li>- Gathering information and plan</li><li>- Dealer change</li><li>- User exchange</li><li>- Prices and payment terms</li><li>- End of contractual relationship</li><li>- Privacy</li><li>- Uncontrollable events</li>
</ul>

<div class="abs copyright">©2021 VINDGERDI - All Right Reserved.</div>

</body>
</html>
```